U.S. Popcorn company needs business cards

We are a popcorn company that manufactures popcorn and sells it to grocery stores worldwide. Our theme is "Americana" and our logo is U.S. route 66 which is the most famous highway in the U.S.

We would like the design to be simple and to use both sides. On the back side we would like to see just the logo and website. The front would be normal details

Target Market(s)

Wholesalers, grocers and distributors

Industry/Entity Type

Manufacture

Contact Information for Business Card

Business name: Prairie Lantern Popcorn
Phone: +1 555 308 4726
Email: Dale@prairielanternpopcorn.com
website: www.prairielanternpopcorn.com
Tag Line: "Kernels Worth Craving"
Name: Dale Whitcombe
Title: Founder/President

Requirements
Must have
• Either this design should be fun or clean and simple. I will let you show me your thougths.
Nice to have
• Anything that ties in the real Hwy Route 66.
• Colors might need to be red, white and blue incorporated.
Should not have
• Not be too busy.

```html
<!DOCTYPE html>
<html lang="en">
<head>
<meta charset="utf-8">
<title>Prairie Lantern Popcorn — Business Card</title>
<link rel="stylesheet" href="https://fonts.googleapis.com/css2?family=Open+Sans:wght@400;600;700&display=swap">
<style>
  :root {
    --stage: #000000;
    --navy: #06266a;
    --red: #e31e24;
    --white: #ffffff;
    --rule: #d0283a;
  }
  * { margin: 0; padding: 0; box-sizing: border-box; }
  html, body { width: 1200px; height: 900px; overflow: hidden; background: var(--stage); }
  body { position: relative; font-family: "Open Sans", Arial, sans-serif; color: var(--white); }

  .card { position: absolute; top: 275px; width: 477px; height: 294px; overflow: hidden; }
  .card--front { left: 116px; background: var(--navy); border-radius: 0 48px 0 48px; }
  .card--back { left: 622px; background: var(--red); border-radius: 48px 0 48px 0; }

  .brand-name {
    position: absolute; left: 0; right: 0; text-align: center;
    font-weight: 700; color: var(--white); text-transform: uppercase; line-height: 1.15;
  }
  .card--front .brand-name { top: 58px; font-size: 22px; letter-spacing: 1px; }
  .card--back .brand-name { top: 108px; font-size: 28px; letter-spacing: 1.5px; }

  .contact-list { position: absolute; left: 20px; top: 165px; list-style: none; }
  .contact-list li { display: flex; align-items: center; height: 17px; font-size: 13px; white-space: nowrap; }
  .contact-list svg { width: 9px; height: 9px; margin-right: 9px; flex: none; }
  .icon-fill { fill: var(--red); }

  .person { position: absolute; right: 27px; top: 178px; text-align: right; white-space: nowrap; }
  .person-name { font-size: 16px; font-weight: 600; line-height: 20px; }
  .person-name .first { color: var(--red); }
  .person-title { font-size: 13px; line-height: 16px; }

  .divider { position: absolute; left: 0; right: 0; top: 232px; height: 1px; background: var(--rule); }

  .tagline {
    position: absolute; left: 0; right: 0; top: 256px; text-align: center;
    font-size: 14.5px; font-weight: 600; letter-spacing: 0.2px; white-space: nowrap;
  }
</style>
</head>
<body>
  <section class="card card--front" aria-label="Card front">
    <div class="brand-name">Prairie Lantern<br>Popcorn</div>

    <ul class="contact-list">
      <li>
        <svg viewBox="0 0 10 10" aria-hidden="true"><path class="icon-fill" d="M2 0.5l1.6 2.2-1 1c.7 1.5 1.6 2.4 3.1 3.1l1-1L9.5 7.4 8.6 9.4C4.5 9.2.8 5.5.6 1.4z"/></svg>
        +1 555 308 4726
      </li>
      <li>
        <svg viewBox="0 0 10 10" aria-hidden="true"><rect class="icon-fill" x="0" y="2" width="10" height="6"/><path d="M0.5 2.5L5 5.5 9.5 2.5" fill="none" stroke="#06266a" stroke-width="1"/></svg>
        Dale@prairielanternpopcorn.com
      </li>
      <li>
        <svg viewBox="0 0 10 10" aria-hidden="true"><circle class="icon-fill" cx="5" cy="5" r="5"/></svg>
        www.prairielanternpopcorn.com
      </li>
    </ul>

    <div class="person">
      <div class="person-name"><span class="first">Dale</span> Whitcombe</div>
      <div class="person-title">Founder/President</div>
    </div>

    <div class="divider"></div>
    <div class="tagline">KERNELS WORTH CRAVING</div>
  </section>

  <section class="card card--back" aria-label="Card back">
    <div class="brand-name">Prairie Lantern<br>Popcorn</div>
  </section>
</body>
</html>
```